design a construction company business card

Design business card around our logo. Card must have all the typical info: name, title, address, phone, email, business name, etc. Somewhere on the card I would like to see our motto "Built on integrity... Inspired by commitment." Consider adding a splash of bright orange to the card to complement the blues and silvers/grays in the logo. We are open to metallic inks, textures, etc. We would like to see options on both light and dark backgrounds. The font in the logo is Euro Technic Extended Regular.

```html
<!DOCTYPE html>
<html lang="en">
<head>
<meta charset="utf-8">
<title>Halvorsen Building – Business Card</title>
<link href="https://fonts.googleapis.com/css2?family=Roboto:ital,wght@0,400;0,700;1,400;1,700&display=swap" rel="stylesheet">
<style>
  :root{
    --stage:#2b2b2e;
    --card-white:#f7f7f8;
    --brand-blue:#1d6fc4;
    --brand-indigo:#3a4fa8;
    --band-blue:#2e6fbf;
    --stripe-gray:#a9adb4;
    --accent-orange:#ff7a1a;
    --text-gray:#4a4d52;
    --muted-gray:#7b7f86;
    --rule-gray:#b7bac0;
    --silver:#c9ccd2;
    --back-top:#2f5fb8;
    --back-bottom:#1c7fd0;
  }
  *{margin:0;padding:0;box-sizing:border-box}
  html,body{width:1200px;height:900px;overflow:hidden}
  body{background:var(--stage);font-family:'Roboto',sans-serif;position:relative}

  .card{position:absolute;left:320px;width:560px;height:320px;border-radius:14px;overflow:hidden;box-shadow:0 14px 30px rgba(0,0,0,.45)}
  .card--front{top:100px;background:var(--card-white)}
  .card--back{top:480px;background:linear-gradient(160deg,var(--back-top),var(--back-bottom))}

  .card__shapes{position:absolute;inset:0}

  .brand{position:absolute;left:44px;top:38px;display:flex;align-items:center;gap:12px;color:var(--brand-indigo);font-weight:700}
  .brand__mark{width:14px;height:14px;background:var(--brand-indigo)}
  .brand__name{font-size:30px;letter-spacing:3px;line-height:1}
  .brand__sub{display:block;font-size:11px;letter-spacing:3px;margin-top:6px}

  .contacts{position:absolute;left:44px;top:132px;list-style:none;font-size:13px;color:var(--text-gray);line-height:20px}
  .contacts li{display:flex;align-items:center;gap:8px}
  .contacts svg{width:11px;height:11px;fill:var(--brand-indigo)}

  .person{position:absolute;right:44px;top:158px;text-align:right}
  .person__name{font-size:25px;font-weight:700;color:var(--brand-blue)}
  .person__title{font-size:14px;font-style:italic;color:var(--muted-gray);margin-top:2px}

  .address{position:absolute;right:44px;top:226px;text-align:right;font-size:13px;color:var(--text-gray);line-height:19px;font-style:normal}
  .website{position:absolute;right:30px;bottom:9px;font-size:13px;color:#fff}

  .back-content{position:absolute;inset:0;display:flex;flex-direction:column;align-items:center;justify-content:center;gap:18px}
  .brand--back{position:static;color:var(--silver)}
  .brand--back .brand__name{font-size:40px}
  .brand--back .brand__sub{font-size:13px}
  .brand--back .brand__mark{width:18px;height:18px;background:var(--silver)}
  .accent-rule{width:60px;height:3px;background:var(--accent-orange)}
  .motto{font-size:14px;font-style:italic;color:#fff;letter-spacing:.5px}
</style>
</head>
<body>

<section class="card card--front" aria-label="Business card front">
  <svg class="card__shapes" viewBox="0 0 560 320" aria-hidden="true">
    <line x1="44" y1="116" x2="516" y2="116" stroke="var(--rule-gray)" stroke-width="1"/>
    <line x1="360" y1="214" x2="516" y2="214" stroke="var(--rule-gray)" stroke-width="1"/>
    <path d="M0,204 C180,250 360,276 560,282 L560,320 L0,320 Z" fill="var(--stripe-gray)"/>
    <path d="M0,211 C175,256 360,282 560,286 L560,320 L0,320 Z" fill="var(--accent-orange)"/>
    <path d="M0,216 C170,262 360,288 560,290 L560,320 L0,320 Z" fill="var(--band-blue)"/>
  </svg>

  <div class="brand">
    <span class="brand__mark"></span>
    <div>
      <span class="brand__name">HALVORSEN</span>
      <span class="brand__sub">BUILDING, INC.</span>
    </div>
  </div>

  <ul class="contacts">
    <li><svg viewBox="0 0 12 12"><path d="M2.5 0.5 L4.5 0.5 L5 3.5 L3.6 4.4 C4.3 6 5.9 7.7 7.6 8.4 L8.5 7 L11.5 7.5 L11.5 9.5 C11.5 10.8 10.6 11.5 9.5 11.5 C4.6 11.2 0.8 7.4 0.5 2.5 C0.5 1.4 1.2 0.5 2.5 0.5 Z"/></svg>555 210 4476</li>
    <li><svg viewBox="0 0 12 12"><path d="M3 0 H9 A1 1 0 0 1 10 1 V11 A1 1 0 0 1 9 12 H3 A1 1 0 0 1 2 11 V1 A1 1 0 0 1 3 0 Z M3.5 1.5 V9.5 H8.5 V1.5 Z"/></svg>555 318 9902</li>
    <li><svg viewBox="0 0 12 12"><path d="M0 2 H12 V10 H0 Z M0.8 2.6 L6 6.6 L11.2 2.6 Z" fill-rule="evenodd"/></svg>info@halvorsenbuild.com</li>
  </ul>

  <div class="person">
    <p class="person__name">Daniel Ward</p>
    <p class="person__title">Director</p>
  </div>

  <address class="address">
    Level 2, 17 Harbour Lane<br>
    Fairview, VIC 3100
  </address>

  <p class="website">www.halvorsenbuild.com</p>
</section>

<section class="card card--back" aria-label="Business card back">
  <div class="back-content">
    <div class="brand brand--back">
      <span class="brand__mark"></span>
      <div>
        <span class="brand__name">HALVORSEN</span>
        <span class="brand__sub">BUILDING, INC.</span>
      </div>
    </div>
    <span class="accent-rule"></span>
    <p class="motto">Built on integrity... Inspired by commitment.</p>
  </div>
</section>

</body>
</html>
```